Reach Crafters Unique Marketing Website Design

I am starting a new company that is a thought leader in the marketing consulting space. The company is called Reach Crafters. We intend to build a Wordpress site on the Astra Theme with the Spectra builder. Our goal is to become the leading voice that empowers high-ticket service business leaders to become Reach Crafters by equipping them with the cutting-edge frameworks and decision grade intelligence taught in leading business schools. What we are looking for is a website design that is clean and professional, making some use of white space well also being eye catching and distinctive in the consulting space. We will probably want to have a video on the homepage not in the hero section, but just below to explain the company and what we do. Our tagline is "Be found. Be chosen." I have attached a brand guide with some messaging, our typography choices, and our color system. The full site will have a primary nav that is four pages - About us, Services, Insights (essentially a blog), and Contact Us. The goal of this project is to develop an art direction that I can give to a designer to build loads of new pages.

Target Market(s)

Business owners (mostly male) from 30-60 years old, looking to fix their sales and marketing funnel.

Industry/Entity Type

Marketing consulting

Font styles to use
Sans Serif

Requirements
Must have
• A clean, professional design that builds trust with owners of high-ticket service businesses. We need a space for explainer video, and sections that tell prospects what we do. Would also like to have a blog carousel.
Nice to have
• Social feeds, if possible. See attached documents for colors and fonts.
Should not have
• Our feel is professional enough to be trustworthy, but unique enough to be memorable. Cartoon ideas do not meet the professional test, and we do not want the website to appear feminine.

```html
<!DOCTYPE html>
<html lang="en">
<head>
<meta charset="UTF-8">
<title>Reach Crafters — Be Found. Be Chosen.</title>
<link rel="stylesheet" href="https://fonts.googleapis.com/css2?family=Oswald:wght@500;600&family=Inter:wght@400;500;600;700&display=swap">
<style>
:root{
  --blue:#2b3cf5;
  --blue-light:#3b8cff;
  --navy:#0a1a4d;
  --navy-deep:#050d2e;
  --ink:#101218;
  --body:#3a3d47;
  --card:#e9ebfd;
  --blog-card:#f1f1f3;
  --white:#ffffff;
}
*{box-sizing:border-box;margin:0;padding:0}
html,body{width:1200px;height:4946px;overflow:hidden;background:var(--white)}
body{font-family:"Inter",sans-serif;color:var(--body);position:relative}
.display{font-family:"Oswald",sans-serif;font-weight:600;text-transform:uppercase;color:var(--ink);letter-spacing:.5px}
section,header,footer{position:absolute;left:0;width:1200px}
.abs{position:absolute}
.btn{position:absolute;display:flex;align-items:center;justify-content:center;border-radius:30px;font-size:13px;font-weight:600;color:var(--white);background:var(--blue)}
.btn-outline{background:transparent;border:2px solid var(--blue)}
.photo{position:absolute;border-radius:10px}

/* Hero */
.hero{top:0;height:563px;background:radial-gradient(ellipse at 30% 20%,#1b2d7a 0%,#0c1c58 45%,#071447 100%)}
.logo{position:absolute;left:100px;top:40px;font-size:22px;font-weight:700;color:#c9cbd6;letter-spacing:.3px}
.nav{position:absolute;top:46px;left:494px;display:flex;gap:28px;font-size:13px;font-weight:500;color:var(--white)}
.nav .current{color:var(--blue-light)}
.hero-title{position:absolute;top:185px;width:100%;text-align:center;font-size:66px;color:var(--white)}
.hero-text{position:absolute;top:280px;width:100%;text-align:center;font-size:14.5px;line-height:26px;color:#e3e6f2}
.hero-text b{color:var(--white)}

/* Intro */
.intro{top:563px;height:760px}
.intro h2{position:absolute;left:172px;top:90px;font-size:52px;line-height:58px}
.divider{position:absolute;width:3px;background:var(--blue);box-shadow:6px 0 0 var(--blue)}
.intro p{position:absolute;left:708px;font-size:14px;line-height:26px}

/* Services */
.services{top:1323px;height:990px}
.center-head{position:absolute;width:100%;text-align:center;font-size:52px}
.center-sub{position:absolute;width:100%;text-align:center;font-size:14px;line-height:26px}
.service-card{position:absolute;width:487px;height:286px;background:var(--card);border-radius:6px;padding:38px 36px}
.service-card svg{display:block;width:62px;height:62px}
.service-card h3{font-size:24px;margin-top:14px}
.service-card p{font-size:14px;line-height:26px;margin-top:14px}

/* Leaders */
.leaders{top:2313px;height:700px}
.leaders h2{position:absolute;left:650px;top:80px;font-size:55px;line-height:57px}
.leaders .lead{position:absolute;left:685px;top:287px;width:410px;font-size:14px;line-height:26px;font-weight:600;color:var(--ink)}
.leaders .copy{position:absolute;left:650px;width:455px;font-size:14px;line-height:26px}

/* Blog */
.blog{top:3013px;height:820px}
.blog-card{position:absolute;top:280px;width:318px;height:400px;background:var(--blog-card);border-radius:8px;overflow:hidden}
.blog-card .thumb{height:210px;border-radius:8px 8px 0 0}
.blog-card h4{margin:38px 36px 0;font-size:17px;font-weight:600;color:var(--ink)}
.blog-card p{margin:12px 36px 0;font-size:14px;line-height:26px}

/* Thinking desk */
.desk{top:3833px;height:715px;background:radial-gradient(ellipse at 50% 20%,#0e1f5f 0%,#071546 55%,#050f36 100%)}
.desk .center-head{color:var(--white)}
.desk .center-sub{color:#dfe3f3}
.desk-card{position:absolute;top:324px;width:231px;height:258px;border-radius:8px}
.arrow{position:absolute;top:442px;width:22px;height:22px}

/* Footer */
.footer{top:4548px;height:398px;background:#050d2e;border-top:1px solid #1e2850}
.footer .brand{position:absolute;left:100px;top:112px;font-size:34px;font-weight:700;color:#c9cbd6}
.footer .tag{position:absolute;left:100px;top:174px;font-size:20px;color:#e3e6f2}
.footer .copy{position:absolute;left:98px;top:270px;font-size:14px;color:#e3e6f2}
.footer-col{position:absolute;top:120px}
.footer-col h5{font-size:16px;font-weight:600;color:var(--white);margin-bottom:18px}
.footer-col li{list-style:none;font-size:14px;color:#dfe3f3;margin-bottom:20px}
</style>
</head>
<body>

<header class="hero">
  <div class="logo">REACH CRAFTERS</div>
  <nav class="nav"><span class="current">Home</span><span>About us</span><span>Services</span><span>Insights</span><span>Contact us</span></nav>
  <a class="btn" style="left:916px;top:33px;width:184px;height:45px">Talk to a Reach Crafter</a>
  <h1 class="display hero-title">Be Found. Be Chosen.</h1>
  <p class="hero-text">We help high-ticket service businesses design demand systems that make growth<br>predictable — using <b>decision-grade intelligence and proven business frameworks.</b></p>
  <a class="btn" style="left:409px;top:371px;width:189px;height:44px">Explore Our Approach</a>
  <a class="btn btn-outline" style="left:620px;top:371px;width:172px;height:44px">See How We Help</a>
</header>

<section class="intro">
  <h2 class="display">Demand is not luck.<br>It’s designed.</h2>
  <div class="divider" style="left:645px;top:98px;height:100px;width:3px;box-shadow:none"></div>
  <div class="divider" style="left:652px;top:98px;height:100px;width:3px;box-shadow:none"></div>
  <p style="top:102px">Most service businesses rely on referrals,<br>reputation, or inconsistent marketing tactics.</p>
  <p style="top:167px;font-weight:600;color:var(--ink)">Reach Crafters exists to change that.</p>
  <div class="photo" role="img" aria-label="Explainer video: team meeting in a bright office around a whiteboard" style="left:174px;top:266px;width:852px;height:451px;background:linear-gradient(135deg,#9aa3a0 0%,#6c7a7c 40%,#4d5a63 70%,#7f8b95 100%)"></div>
  <svg class="abs" style="left:573px;top:468px" width="52" height="52" viewBox="0 0 52 52"><circle cx="26" cy="26" r="26" fill="#2b3cf5"/><path d="M20 15 L38 26 L20 37 Z" fill="#fff"/></svg>
</section>

<section class="services">
  <h2 class="display center-head" style="top:100px">What we do</h2>
  <p class="center-sub" style="top:180px">We work with high-ticket service businesses to move from reactive<br>marketing to intentional demand creation.</p>

  <article class="service-card" style="left:100px;top:287px">
    <svg viewBox="0 0 62 62"><path d="M8 14h12a6 6 0 1 1 10 0h12v12a6 6 0 1 1 0 10v12H30a6 6 0 1 0-10 0H8V36a6 6 0 1 0 0-10Z" fill="#2b3cf5"/></svg>
    <h3 class="display">Demand Strategy</h3>
    <p>Define where demand should come from, who it should target, and how it should convert — before investing in execution.</p>
  </article>

  <article class="service-card" style="left:613px;top:318px">
    <svg viewBox="0 0 62 62"><circle cx="31" cy="31" r="26" fill="#2b3cf5"/><path d="M31 8v46M22 20h9M31 30h10M22 40h9" stroke="#fff" stroke-width="2.5" fill="none"/><circle cx="44" cy="30" r="3" fill="#fff"/></svg>
    <h3 class="display">Decision-Grade Intelligence</h3>
    <p>Replace assumptions with insight through customer research, market analysis, and signal-driven decision making.</p>
  </article>

  <article class="service-card" style="left:100px;top:602px">
    <svg viewBox="0 0 62 62"><path d="M31 10a15 15 0 0 1 9 27v7H22v-7a15 15 0 0 1 9-27Z" fill="#2b3cf5"/><rect x="23" y="47" width="16" height="5" rx="2" fill="#2b3cf5"/><path d="M6 24h5M51 24h5M12 9l4 4M50 9l-4 4M8 40l4-3M54 40l-4-3" stroke="#2b3cf5" stroke-width="3" stroke-linecap="round"/></svg>
    <h3 class="display">Positioning &amp; Narrative</h3>
    <p>Clarify your value so the right buyers understand why to choose you — and do so faster.</p>
  </article>

  <article class="service-card" style="left:613px;top:629px">
    <svg viewBox="0 0 62 62"><circle cx="31" cy="31" r="26" fill="#2b3cf5"/><path d="M42 19c-10 1-17 8-19 19l-3 5 4-2c10-1 17-9 18-22Z" fill="#fff"/></svg>
    <h3 class="display">Go-To-Market Advisory</h3>
    <p>Ongoing guidance to help leadership teams make better marketing and growth decisions with confidence.</p>
  </article>
</section>

<section class="leaders">
  <div class="photo" role="img" aria-label="Photo of two colleagues reviewing work on a tablet" style="left:100px;top:75px;width:478px;height:558px;background:linear-gradient(150deg,#cdbfae 0%,#a8907a 45%,#6e5a4c 100%)"></div>
  <h2 class="display">Built for leaders<br>who take demand<br>seriously.</h2>
  <div class="divider" style="left:652px;top:290px;height:72px;width:3px;box-shadow:none"></div>
  <div class="divider" style="left:659px;top:290px;height:72px;width:3px;box-shadow:none"></div>
  <p class="lead">Reach Crafters is a marketing consulting firm focused on one thing: helping high-ticket service businesses create intentional, reliable demand.</p>
  <p class="copy" style="top:384px">Too many firms grow through referrals, reputation, or isolated marketing tactics — approaches that work until they don’t. When growth stalls or becomes unpredictable, the problem is rarely effort. It’s clarity.</p>
  <p class="copy" style="top:488px">Reach Crafters exists to help leaders stop guessing, start choosing, and build demand systems that support long-term growth.</p>
  <a class="btn" style="left:650px;top:573px;width:127px;height:44px">Learn More</a>
</section>

<section class="blog">
  <h2 class="display center-head" style="top:100px">Latest Blog</h2>
  <p class="center-sub" style="top:180px">We work with high-ticket service businesses to move from reactive<br>marketing to intentional demand creation.</p>
  <article class="blog-card" style="left:100px">
    <div class="thumb" role="img" aria-label="Photo of hands reviewing charts on a tablet" style="background:linear-gradient(135deg,#1e2a44,#5a6a86 60%,#c9ced8)"></div>
    <h4>Nam libero tempore</h4>
    <p>Nam libero tempore, cum soluta nobis est eligendi optio cumque nihil impedit quo minus</p>
  </article>
  <article class="blog-card" style="left:440px">
    <div class="thumb" role="img" aria-label="Photo of a speaker presenting to a small audience" style="background:linear-gradient(135deg,#6f7780,#3a3f47 60%,#8a9097)"></div>
    <h4>Nam libero tempore</h4>
    <p>Nam libero tempore, cum soluta nobis est eligendi optio cumque nihil impedit quo minus</p>
  </article>
  <article class="blog-card" style="left:780px">
    <div class="thumb" role="img" aria-label="Photo of a presenter at a whiteboard in a workshop" style="background:linear-gradient(135deg,#d6d9de,#8c939c 55%,#3d434c)"></div>
    <h4>Nam libero tempore</h4>
    <p>Nam libero tempore, cum soluta nobis est eligendi optio cumque nihil impedit quo minus</p>
  </article>
</section>

<section class="desk">
  <h2 class="display center-head" style="top:130px">From our thinking desk</h2>
  <p class="center-sub" style="top:218px">Ongoing perspectives on demand, positioning, and growth.</p>
  <svg class="arrow" style="left:56px" viewBox="0 0 22 22"><path d="M14 4 7 11l7 7" stroke="#fff" stroke-width="2.5" fill="none"/></svg>
  <div class="desk-card" role="img" aria-label="Image of data analytics dashboard" style="left:100px;background:linear-gradient(135deg,#2a2f6e,#7a4f8a 50%,#c58a3c)"></div>
  <div class="desk-card" role="img" aria-label="Photo of a desk with charts and sticky notes" style="left:356px;background:linear-gradient(135deg,#e8e3da,#b8b3ab 55%,#6d6a66)"></div>
  <div class="desk-card" role="img" aria-label="Photo of colleagues working together on a laptop" style="left:613px;background:linear-gradient(135deg,#d9d6d1,#9c8d7e 55%,#5c4f44)"></div>
  <div class="desk-card" role="img" aria-label="Photo of a workspace with digital network graphics" style="left:870px;background:linear-gradient(135deg,#b8c8cc,#8a7a5c 55%,#d08a3a)"></div>
  <svg class="arrow" style="left:1124px" viewBox="0 0 22 22"><path d="M8 4l7 7-7 7" stroke="#fff" stroke-width="2.5" fill="none"/></svg>
</section>

<footer class="footer">
  <div class="brand">REACH CRAFTERS</div>
  <div class="tag">Be found. Be chosen.</div>
  <div class="copy">2026 Reach Crafters. All Rights Reserved.</div>
  <div class="footer-col" style="left:589px"><h5>Quick Links</h5><ul><li>About Us</li><li>Services</li><li>Insights</li><li>Contact Us</li></ul></div>
  <div class="footer-col" style="left:785px"><h5>Other Links</h5><ul><li>Terms &amp; Conditions</li><li>Privacy &amp; Policy</li><li>Cookies</li><li>Help</li></ul></div>
  <div class="footer-col" style="left:1020px"><h5>Follow Us</h5><ul><li>ProNet</li><li>ClipStream</li></ul></div>
</footer>

</body>
</html>
```